BRISKEL Need a luxury modern business card designed.

Need a luxury modern business card designed. refer to the uploaded files for the company name and logo in the zip file under source files. i will making my descion on monday. so please send in before then so if we need to edit we will have the time. we have a trade show coming up and im on a deadline for printer.

Target Market(s)

high end clients

Contact Information for Business Card

Company nAme and logo. Tobias Fennick Co-Founder / Project Manager Office # 555-318-7094 Cell # 555-642-1586 BRISKEL.CA Tobias@briskel-example.ca

Font styles to use
Other font styles liked:
• Modern

Requirements
Must have
• Company name and logo, contact info, using the black, gold and white color scheme.

```html
<!DOCTYPE html>
<html lang="en">
<head>
<meta charset="utf-8">
<title>BRISKEL Business Card</title>
<link href="https://fonts.googleapis.com/css2?family=Kanit:wght@200;300;400&display=swap" rel="stylesheet">
<style>
  :root {
    --backdrop: #b48a5c;
    --card: #26272a;
    --gold: #8f8660;
    --white: #f2f2f0;
    --shadow: rgba(40, 24, 10, 0.45);
  }
  * { margin: 0; padding: 0; box-sizing: border-box; }
  html, body {
    width: 1200px; height: 859px; overflow: hidden;
    background: var(--backdrop);
    font-family: "Kanit", sans-serif;
  }
  .canvas { position: relative; width: 1200px; height: 859px; }
  .card {
    position: absolute; top: 288px;
    width: 500px; height: 285px;
    background: var(--card);
    overflow: hidden;
    box-shadow: 0 10px 18px var(--shadow);
  }
  .card--front { left: 60px; }
  .card--back { left: 639px; }
  .card__stripes { position: absolute; inset: 0; }

  .wordmark {
    position: absolute; left: 22px; top: 30px;
    font-weight: 200; font-size: 21px; letter-spacing: 5px;
    color: var(--white); line-height: 1;
  }

  .person { position: absolute; left: 21px; top: 110px; }
  .person__marker {
    position: absolute; left: -21px; top: 4px;
    width: 2px; height: 28px; background: var(--gold);
  }
  .person__name {
    font-weight: 400; font-size: 16px; letter-spacing: 0.4px;
    color: var(--gold); line-height: 1.1;
    text-transform: uppercase;
  }
  .person__role {
    font-weight: 300; font-size: 12.5px; color: var(--white);
    margin-top: 4px;
  }

  .contacts { position: absolute; left: 21px; top: 191px; list-style: none; }
  .contacts li {
    display: flex; align-items: center; gap: 6px;
    height: 17.5px;
    font-weight: 300; font-size: 12.5px; color: var(--white);
  }
  .contacts svg { width: 11px; height: 11px; flex: none; }
  .contacts .accent { color: var(--gold); }

  .brand-center {
    position: absolute; left: 0; right: 0; top: 120px;
    display: flex; flex-direction: column; align-items: center; gap: 22px;
  }
  .brand-center__square {
    width: 26px; height: 26px; border: 2px solid var(--gold);
  }
  .brand-center__name {
    font-weight: 200; font-size: 33px; letter-spacing: 9px;
    color: var(--white); line-height: 1; padding-left: 9px;
  }
</style>
</head>
<body>
<main class="canvas">

  <section class="card card--front" aria-label="Business card front">
    <svg class="card__stripes" viewBox="0 0 500 285" aria-hidden="true">
      <polygon points="289,285 500,75 500,150 364,285" fill="var(--gold)"/>
      <polygon points="441,285 500,227 500,285" fill="var(--gold)"/>
    </svg>

    <div class="wordmark">BRISKEL</div>

    <div class="person">
      <span class="person__marker"></span>
      <h1 class="person__name">Tobias Fennick</h1>
      <p class="person__role">Co-Founder | Project Manager</p>
    </div>

    <ul class="contacts">
      <li>
        <svg viewBox="0 0 12 12" fill="none" stroke="var(--gold)" stroke-width="0.9"><circle cx="6" cy="6" r="5.2"/><path d="M4 3.4l1 1.5-.6.6c.4.9 1.1 1.6 2 2l.6-.6 1.5 1-.6 1c-2.2-.3-4.2-2.3-4.5-4.5z"/></svg>
        555-318-7094
      </li>
      <li>
        <svg viewBox="0 0 12 12" fill="none" stroke="var(--gold)" stroke-width="0.9"><rect x="3.5" y="1" width="5" height="10" rx="0.8"/><line x1="5.3" y1="9.5" x2="6.7" y2="9.5"/></svg>
        555-642-1586
      </li>
      <li>
        <svg viewBox="0 0 12 12" fill="none" stroke="var(--gold)" stroke-width="0.9"><rect x="0.8" y="2.5" width="10.4" height="7" /><path d="M0.8 2.5l5.2 4 5.2-4"/></svg>
        Tobias@briskel-example.ca
      </li>
      <li>
        <svg viewBox="0 0 12 12" fill="none" stroke="var(--gold)" stroke-width="0.9"><circle cx="6" cy="6" r="5.2"/><ellipse cx="6" cy="6" rx="2.3" ry="5.2"/><line x1="0.8" y1="6" x2="11.2" y2="6"/></svg>
        <span>www.<span class="accent">briskel</span>.ca</span>
      </li>
    </ul>
  </section>

  <section class="card card--back" aria-label="Business card back">
    <svg class="card__stripes" viewBox="0 0 500 285" aria-hidden="true">
      <polygon points="0,74 67,0 143,0 0,144" fill="var(--gold)"/>
    </svg>
    <div class="brand-center">
      <span class="brand-center__square"></span>
      <div class="brand-center__name">BRISKEL</div>
    </div>
  </section>

</main>
</body>
</html>
```